Business Card Design

Electronic Security
Alarm Systems
CCTV
Electronic Access Control
Security System Integration

Industry/Entity Type

Business

Contact Information for Business Card

Gareth Linwood
PO Box 862
Ashgrove Qld 4071
Phone 07 38526147
Mob 0427395816

```html
<!DOCTYPE html>
<html lang="en">
<head>
<meta charset="utf-8">
<title>Gareth Linwood – Business Card</title>
<link href="https://fonts.googleapis.com/css2?family=Archivo+Black&family=Arimo:wght@400;700&display=swap" rel="stylesheet">
<style>
  :root {
    --page: #e9eaec;
    --card-white: #ffffff;
    --band-blue: #1a8fb8;
    --band-blue-deep: #157ea3;
    --accent-yellow: #f2bd12;
    --ink: #111111;
    --icon-blue: #1b86b0;
    --brand-grey: #3a3f45;
  }
  * { margin: 0; padding: 0; box-sizing: border-box; }
  html, body {
    width: 1200px; height: 848px; overflow: hidden;
    background: var(--page);
  }
  .stage {
    width: 1200px; height: 848px;
    display: flex; align-items: center; justify-content: center;
  }
  .card {
    position: relative;
    width: 900px; height: 550px;
    background: var(--card-white);
    border-radius: 34px;
    overflow: hidden;
    box-shadow: 0 10px 30px rgba(0,0,0,.18);
  }
  .card__wave {
    position: absolute; left: 0; top: 0;
    width: 900px; height: 550px;
  }
  .holder-name {
    position: absolute; left: 92px; top: 62px;
    font-family: "Archivo Black", "Arial Black", sans-serif;
    font-size: 44px; letter-spacing: 1px; word-spacing: 14px;
    color: var(--ink);
  }
  .contact-list {
    position: absolute; left: 92px; top: 150px;
    list-style: none;
    font-family: "Arimo", Arial, sans-serif;
    font-size: 25px; color: var(--ink);
  }
  .contact-list li {
    display: flex; align-items: center;
    height: 46px;
  }
  .contact-list svg {
    width: 26px; height: 26px; margin-right: 34px;
    fill: var(--icon-blue);
  }
  .brand {
    position: absolute; right: 70px; top: 205px;
    display: flex; align-items: center; gap: 14px;
    font-family: "Arimo", Arial, sans-serif;
    font-weight: 400; font-size: 52px; letter-spacing: 2px;
    color: var(--brand-grey);
  }
  .brand__mark {
    width: 22px; height: 22px;
    background: var(--band-blue);
  }
</style>
</head>
<body>
<main class="stage">
  <article class="card">
    <svg class="card__wave" viewBox="0 0 900 550" aria-hidden="true">
      <path d="M0 318 C 180 300, 330 310, 470 352 C 610 392, 760 370, 900 338 L900 550 L0 550 Z" fill="var(--accent-yellow)"/>
      <path d="M0 332 C 180 314, 330 324, 470 366 C 610 406, 760 384, 900 352 L900 550 L0 550 Z" fill="var(--band-blue)"/>
    </svg>

    <h1 class="holder-name">Gareth Linwood</h1>

    <ul class="contact-list">
      <li>
        <svg viewBox="0 0 24 24" aria-label="Phone"><path d="M3 9c0-3 4-5 9-5s9 2 9 5v2h-5V9c-1-.6-2.4-1-4-1s-3 .4-4 1v2H3zM7 12h10l3 7H4z"/></svg>
        07 38526147
      </li>
      <li>
        <svg viewBox="0 0 24 24" aria-label="Mobile"><path d="M7 2h10a1 1 0 0 1 1 1v18a1 1 0 0 1-1 1H7a1 1 0 0 1-1-1V3a1 1 0 0 1 1-1zm1 3v6h8V5zm0 8v2h2v-2zm3 0v2h2v-2zm3 0v2h2v-2zm-6 3v2h2v-2zm3 0v2h2v-2zm3 0v2h2v-2z"/></svg>
        0427395816
      </li>
      <li>
        <svg viewBox="0 0 24 24" aria-label="Address"><path d="M12 3l10 9h-3v9h-5v-6h-4v6H5v-9H2z"/></svg>
        PO Box 862 Ashgrove Qld 4071
      </li>
    </ul>

    <div class="brand">
      <span class="brand__mark"></span>
      <span class="brand__name">KELTA</span>
    </div>
  </article>
</main>
</body>
</html>
```